Road Construction Company needs business cards

We would like a new business card designed for our business.

We're a road construction company based in Qld, Australia.

Can the business card please have the following information on it.

Name: Warren Halbeck
Position: General Manager
Phone: 0472 915 348
Email: Warren.halbeck@tovrin.com.au
Address: 87 Marrow Ave, Pendlebay, QLD, 4023
Website: www.tovrin.com.au

Visually we'd like the card to be professional and simple.

Attached is our logo.

Our website is www.tovrin.com.au

Target Market(s)

Men aged 25-60

Contact Information for Business Card

As listed in project description

Font styles to use
Serif

Requirements
Must have
• Large logo on back of card

```html
<!DOCTYPE html>
<html lang="en">
<head>
<meta charset="utf-8">
<title>Tovrin Business Card</title>
<link rel="stylesheet" href="https://fonts.googleapis.com/css2?family=Montserrat:wght@700;800&family=Questrial&display=swap">
<style>
  :root {
    --bg: #e4e5e8;
    --card-white: #ffffff;
    --brand-blue: #1a4c9c;
    --accent-blue: #2a8fd4;
    --text-grey: #555a61;
    --rule-grey: #8a8e94;
    --back-light: #2aa0d8;
    --back-mid: #1673c0;
    --back-dark: #124f9e;
  }
  * { box-sizing: border-box; margin: 0; padding: 0; }
  html, body { width: 1200px; height: 800px; overflow: hidden; }
  body {
    background: var(--bg);
    font-family: "Questrial", sans-serif;
    position: relative;
  }
  .card {
    position: absolute;
    top: 250px;
    width: 520px;
    height: 300px;
    box-shadow: 0 6px 18px rgba(0,0,0,0.12);
  }
  .card-back {
    left: 50px;
    background: radial-gradient(circle at 50% 42%, var(--back-light) 0%, var(--back-mid) 45%, var(--back-dark) 100%);
    color: #fff;
  }
  .back-wordmark {
    position: absolute;
    left: 0; right: 0; top: 92px;
    text-align: center;
    font-family: "Montserrat", sans-serif;
    font-weight: 800;
    font-size: 48px;
    letter-spacing: 3px;
  }
  .back-rule {
    position: absolute;
    left: 130px; right: 130px; top: 172px;
    height: 1px;
    background: rgba(255,255,255,0.85);
  }
  .back-web {
    position: absolute;
    left: 0; right: 0; top: 184px;
    text-align: center;
    font-size: 14px;
    letter-spacing: 5px;
  }
  .card-front {
    left: 630px;
    background: var(--card-white);
  }
  .holder-name {
    position: absolute;
    left: 40px; top: 32px;
    font-family: "Montserrat", sans-serif;
    font-weight: 700;
    font-size: 19px;
    color: var(--brand-blue);
    text-transform: uppercase;
    letter-spacing: 0.3px;
  }
  .holder-title {
    position: absolute;
    left: 40px; top: 56px;
    font-size: 13px;
    color: var(--text-grey);
  }
  .contact-list {
    position: absolute;
    left: 40px; top: 86px;
    list-style: none;
  }
  .contact-item {
    display: flex;
    align-items: center;
    gap: 7px;
    height: 20px;
    font-size: 12.5px;
    color: var(--text-grey);
  }
  .contact-item svg { width: 12px; height: 12px; flex: none; }
  .divider {
    position: absolute;
    left: 0; right: 0; top: 168px;
    height: 1px;
    background: var(--rule-grey);
  }
  .front-wordmark {
    position: absolute;
    left: 30px; top: 180px;
    font-family: "Montserrat", sans-serif;
    font-weight: 800;
    font-size: 46px;
    letter-spacing: 2px;
    color: var(--brand-blue);
  }
  .address {
    position: absolute;
    right: 34px; bottom: 26px;
    text-align: right;
    font-size: 14px;
    line-height: 19px;
    color: var(--text-grey);
  }
</style>
</head>
<body>
  <section class="card card-back" aria-label="Card back">
    <div class="back-wordmark">TOVRIN</div>
    <div class="back-rule"></div>
    <div class="back-web">www.tovrin.com.au</div>
  </section>

  <section class="card card-front" aria-label="Card front">
    <h1 class="holder-name">Warren Halbeck</h1>
    <p class="holder-title">General Manager</p>
    <ul class="contact-list">
      <li class="contact-item">
        <svg viewBox="0 0 12 12" aria-hidden="true"><path d="M2.5 1 L4.5 1 L5 3.5 L3.8 4.5 Q5 7 7.5 8.2 L8.5 7 L11 7.5 L11 9.5 Q10.5 11 9 11 Q2 10 1 3 Q1 1.5 2.5 1 Z" fill="var(--accent-blue)"/></svg>
        <span>0472 915 348</span>
      </li>
      <li class="contact-item">
        <svg viewBox="0 0 12 12" aria-hidden="true"><circle cx="6" cy="6" r="5" fill="none" stroke="var(--accent-blue)" stroke-width="1.2"/><ellipse cx="6" cy="6" rx="2.2" ry="5" fill="none" stroke="var(--accent-blue)" stroke-width="1"/><line x1="1" y1="6" x2="11" y2="6" stroke="var(--accent-blue)" stroke-width="1"/></svg>
        <span>www.tovrin.com.au</span>
      </li>
      <li class="contact-item">
        <svg viewBox="0 0 12 12" aria-hidden="true"><rect x="0.5" y="2.5" width="11" height="7.5" rx="1" fill="var(--accent-blue)"/><path d="M1 3 L6 7 L11 3" fill="none" stroke="#fff" stroke-width="1"/></svg>
        <span>Warren.halbeck@tovrin.com.au</span>
      </li>
    </ul>
    <div class="divider"></div>
    <div class="front-wordmark">TOVRIN</div>
    <address class="address" style="font-style:normal">87 Marrow Ave<br>Pendlebay, QLD, 4023</address>
  </section>
</body>
</html>
```